wordpress website Carla Winfield, Author, Speaker and Coach

Need a wordpress blogging website for author/speaker/coach.
I have paid for hosting on nestparrot.
I am currently writing a book - Launchpad to Campus - Steps and strategies to prepare you to thrive in college and beyond. Eventually, I will have an Academic/Life Coaching program targeting high school and college students. This website's purpose is to build my email list. I can offer the following reports as incentive for email sign-up:
1. Six Habits That Get Your Teen Through University On Schedule and Debt-Light
2. Surprising Routes to Fund Your Degree
3. SAT/ACT vocabulary word of the day

facebook page: https://www.facebook.com/Carla-Winfield-AcademicLife-Coach-918273645501928/

I would like to have these pages:

1. Home or About page

High school is becoming more and more stressful for students. Not only are they taking more AP classes than ever before, and often spending $1,000’s on SAT/ACT prep programs, most are NOT prepared for success in college. Only 19% of students are graduating from college within 4 years and only 56% are graduating within 6 years. With the cost of higher education skyrocketing, each extra year of school can costs families $40,000 - $60,000 when you factor in living expenses. Then, when students do graduate, they are often underemployed.

Carla's approach is whole person oriented. Her programs help students learn life skills in addition to the study, time management skills, etc. offered by most academic coaching programs. Our program addresses all of the major causes of failure to graduate within 4 years, and is based on sound educational research. Carla's program initially provides the daily interaction needed to successfully change behaviors and seat new success habits, unlike many programs in which students interact with coaches only once a week.
Bio
Carla Winfield is a certified teacher and holds advanced certification in academic coaching and tutoring. She also is a certified trainer in the Morris Tellwright Achievement Keys. She has three successful adult children, and helped them overcome learning differences and thrive.

2. Blog

3. Contact - Include form (I split time between USA and Saudi Arabia, so I will call or email people back, but don't want to leave a phone number)
info@carlawinfield.example

4. Store – 1 book for now
Launchpad to Campus
Steps and strategies to prepare you to thrive in college and beyond
Available 12/01/2017
I could make a preview chapter available for download

5. Speaking
Carla Winfield is available for keynote addresses and half-day, full day or multi-day workshops. I will develop details later

6.Coaching programs
I will develop details later

Target Market(s)

high school students who are college bound and their parents

Number of Pages Required

5+ page

Font styles to use
Sans Serif

Colors

Designer to choose colors to be used in the design.

Requirements
Nice to have
• integration with post finch for contact management

```html
<!DOCTYPE html>
<html lang="en">
<head>
<meta charset="utf-8">
<title>Carla Winfield – Academic/Life Coaching</title>
<link rel="stylesheet" href="https://fonts.googleapis.com/css2?family=Open+Sans:wght@300;400;600&family=Source+Sans+3:wght@700;900&display=swap">
<style>
  :root {
    --green: #1f8e56;
    --green-dark: #0f7a3e;
    --green-footer: #137a3b;
    --btn-green: #0b7a3d;
    --nav-active: #1f8e56;
    --ink: #333333;
    --muted: #555555;
    --light-bg: #f5f5f5;
    --white: #ffffff;
    --purple: #8a86c8;
    --teal: #3fae7a;
    --lime: #8cc63f;
  }
  * { box-sizing: border-box; margin: 0; padding: 0; }
  html, body { width: 1200px; height: 2466px; overflow: hidden; }
  body { position: relative; font-family: "Open Sans", Arial, sans-serif; color: var(--ink); background: var(--white); }

  /* Header */
  .site-header { position: absolute; top: 0; left: 0; width: 1200px; height: 123px; background: var(--white); z-index: 2; }
  .brand { position: absolute; left: 99px; top: 42px; display: flex; align-items: center; gap: 14px; font-family: "Open Sans", sans-serif; font-size: 27px; font-weight: 400; color: #444; }
  .brand-dot { width: 26px; height: 26px; border-radius: 50%; background: var(--green); }
  .main-nav { position: absolute; top: 55px; left: 0; width: 1200px; font-size: 15px; color: #444; }
  .main-nav a { position: absolute; color: inherit; text-decoration: none; white-space: nowrap; }
  .main-nav a.active { color: var(--nav-active); }

  /* Hero */
  .hero { position: absolute; top: 123px; left: 0; width: 1200px; height: 615px; }
  .hero-photo { position: absolute; inset: 0; background: radial-gradient(ellipse at 50% 20%, #5a4a44 0%, #2e2522 45%, #0e0b0a 100%); }
  .hero-title { position: absolute; top: 322px; width: 100%; text-align: center; font-family: "Source Sans 3", sans-serif; font-weight: 700; font-size: 56px; letter-spacing: 1px; color: var(--white); }
  .hero-text { position: absolute; top: 400px; left: 160px; width: 880px; text-align: center; font-size: 13px; line-height: 22px; color: #eee; }
  .hero-btn { position: absolute; top: 487px; left: 519px; width: 162px; height: 36px; border-radius: 18px; background: var(--btn-green); color: var(--white); font-size: 13px; line-height: 36px; text-align: center; }
  .slider-dots { position: absolute; top: 663px; left: 562px; display: flex; gap: 6px; }
  .slider-dots span { width: 16px; height: 16px; border-radius: 50%; background: var(--white); }
  .slider-dots span.current { background: transparent; border: 2px solid var(--white); }

  /* About */
  .about { position: absolute; top: 738px; left: 0; width: 1200px; height: 544px; background: var(--green); color: var(--white); }
  .about-title { position: absolute; top: 90px; left: 99px; font-size: 31px; font-weight: 300; }
  .about-text { position: absolute; top: 140px; left: 99px; width: 585px; font-size: 12.5px; line-height: 25px; }
  .about-text p + p { margin-top: 25px; }
  .outline-btn { position: absolute; top: 405px; left: 99px; width: 199px; height: 41px; border: 1.5px solid rgba(255,255,255,.8); border-radius: 21px; font-size: 14px; line-height: 38px; text-align: center; }
  .portrait-frame { position: absolute; top: 100px; left: 748px; width: 353px; height: 364px; background: var(--white); border-radius: 8px; padding: 7px; }
  .portrait { width: 100%; height: 100%; background: linear-gradient(160deg, #3a302c 0%, #6b4b3f 45%, #1a1412 100%); }

  /* Programs */
  .programs { position: absolute; top: 1282px; left: 0; width: 1200px; height: 526px; background: var(--light-bg); }
  .section-title { position: absolute; width: 100%; text-align: center; font-size: 31px; font-weight: 300; color: #333; }
  .programs .section-title { top: 78px; }
  .program { position: absolute; top: 178px; width: 300px; text-align: center; }
  .program-icon { width: 124px; height: 124px; margin: 0 auto; border-radius: 50%; border: 5px solid rgba(255,255,255,.6); display: flex; align-items: center; justify-content: center; }
  .program-name { margin-top: 20px; font-size: 27px; font-weight: 300; color: #333; }
  .program-text { margin: 10px auto 0; width: 240px; font-size: 13px; line-height: 23px; color: var(--muted); }

  /* Sign-up */
  .signup { position: absolute; top: 1808px; left: 0; width: 1200px; height: 403px; background: var(--white); border-top: 3px solid #eee; }
  .signup .section-title { top: 68px; }
  .offer-list { position: absolute; top: 135px; left: 423px; list-style: none; font-size: 13px; line-height: 26.5px; color: var(--muted); }
  .email-field { position: absolute; top: 257px; left: 197px; width: 563px; height: 43px; border: 1px solid #ddd; font-size: 12px; color: #aaa; padding: 13px 16px; }
  .signup-btn { position: absolute; top: 257px; left: 794px; width: 209px; height: 41px; border-radius: 21px; background: var(--btn-green); color: var(--white); font-size: 17px; line-height: 41px; text-align: center; }

  /* Footer */
  .site-footer { position: absolute; top: 2211px; left: 0; width: 1200px; height: 255px; background: var(--green-footer); color: var(--white); }
  .footer-brand { position: absolute; top: 88px; left: 99px; display: flex; align-items: center; gap: 12px; font-size: 24px; font-weight: 400; }
  .footer-brand .brand-dot { background: var(--white); }
  .cert-badge { position: absolute; top: 38px; left: 534px; width: 132px; height: 132px; border-radius: 50%; background: var(--white); display: flex; align-items: center; justify-content: center; }
  .cert-badge span { width: 96px; height: 96px; border-radius: 50%; background: linear-gradient(135deg, #e4e4e4, #9a9a9a); }
  .social { position: absolute; top: 73px; left: 854px; display: flex; gap: 9px; }
  .social a { width: 42px; height: 42px; border-radius: 50%; background: var(--white); }
  .footer-rule { position: absolute; top: 197px; left: 99px; width: 1002px; height: 1px; background: rgba(255,255,255,.25); }
  .copyright { position: absolute; top: 216px; width: 100%; text-align: center; font-size: 11px; color: rgba(255,255,255,.8); }
</style>
</head>
<body>

<header class="site-header">
  <div class="brand"><span class="brand-dot"></span>Carla Winfield</div>
  <nav class="main-nav">
    <a class="active" style="left:567px">Home</a>
    <a style="left:649px">Blog</a>
    <a style="left:721px">Store</a>
    <a style="left:799px">Speaking</a>
    <a style="left:899px">Coaching Program</a>
    <a style="left:1053px">Contact</a>
  </nav>
</header>

<section class="hero">
  <div class="hero-photo" role="img" aria-label="Large audience seated in a lecture hall, dark warm tones"></div>
  <h1 class="hero-title">ACADEMIC/LIFE COACHING PROGRAM</h1>
  <p class="hero-text">Carla Winfield is a certified teacher and holds advanced certification in academic coaching and tutoring. She also is a certified trainer in the Morris Tellwright Achievement Keys. She has three successful adult children, and helped them overcome learning differences and thrive.</p>
  <div class="hero-btn">LEARN MORE &gt;&gt;</div>
  <div class="slider-dots"><span class="current"></span><span></span><span></span><span></span></div>
</section>

<section class="about">
  <h2 class="about-title">ABOUT US</h2>
  <div class="about-text">
    <p>High school is becoming more and more stressful for students. Not only are they taking more AP classes than ever before, and often spending $1,000’s on SAT/ACT prep programs, most are NOT prepared for success in college. Only 19% of students are graduating from college within 4 years and only 56% are graduating within 6 years. With the cost of higher education skyrocketing, each extra year of school can costs families $40,000 - $60,000 when you factor in living expenses. Then, when students do graduate, they are often underemployed.</p>
    <p>Carla’s approach is whole person oriented. Her programs help students learn life skills in addition to the study, time management skills, etc. offered by most academic coaching programs.</p>
  </div>
  <div class="outline-btn">LEARN MORE &gt;&gt;</div>
  <div class="portrait-frame"><div class="portrait" role="img" aria-label="Portrait photograph of Carla Winfield"></div></div>
</section>

<section class="programs">
  <h2 class="section-title">ACADEMIC COACHING PROGRAMS</h2>
  <div class="program" style="left:69px">
    <div class="program-icon" style="background:var(--purple)">
      <svg width="56" height="50" viewBox="0 0 56 50" fill="none" stroke="#fff" stroke-width="3">
        <rect x="6" y="4" width="44" height="11" rx="2"/><rect x="2" y="19" width="48" height="11" rx="2"/><rect x="6" y="34" width="46" height="11" rx="2"/>
      </svg>
    </div>
    <h3 class="program-name">Learn Life Skills</h3>
    <p class="program-text">Excepteur sint occaecat cupidatat non proident sunt in culpa qui officia deserunt mollit anim id est laborum</p>
  </div>
  <div class="program" style="left:450px">
    <div class="program-icon" style="background:var(--teal)">
      <svg width="60" height="56" viewBox="0 0 60 56" fill="#fff">
        <rect x="24" y="4" width="32" height="22" fill="none" stroke="#fff" stroke-width="3"/>
        <circle cx="14" cy="14" r="5"/><rect x="9" y="21" width="10" height="14" rx="3"/>
        <circle cx="14" cy="42" r="4"/><circle cx="30" cy="42" r="4"/><circle cx="46" cy="42" r="4"/>
        <rect x="9" y="47" width="10" height="8" rx="3"/><rect x="25" y="47" width="10" height="8" rx="3"/><rect x="41" y="47" width="10" height="8" rx="3"/>
      </svg>
    </div>
    <h3 class="program-name">Coaching</h3>
    <p class="program-text">Excepteur sint occaecat cupidatat non proident sunt in culpa qui officia deserunt mollit anim id est laborum</p>
  </div>
  <div class="program" style="left:831px">
    <div class="program-icon" style="background:var(--lime)">
      <svg width="58" height="54" viewBox="0 0 58 54" fill="none" stroke="#fff" stroke-width="3">
        <circle cx="22" cy="30" r="18"/><path d="M22 19v11l8 5"/>
        <circle cx="44" cy="16" r="7" fill="#fff"/><path d="M34 38c0-8 5-12 10-12s10 4 10 12z" fill="#fff" stroke="none"/>
      </svg>
    </div>
    <h3 class="program-name">Time Management</h3>
    <p class="program-text">Excepteur sint occaecat cupidatat non proident sunt in culpa qui officia deserunt mollit anim id est laborum</p>
  </div>
</section>

<section class="signup">
  <h2 class="section-title">JOIN OUR EMAIL SIGN-UP</h2>
  <ol class="offer-list">
    <li>1. Six Habits That Get Your Teen Through University On Schedule and Debt-Light</li>
    <li>2. Surprising Routes to Fund Your Degree</li>
    <li>3. SAT/ACT vocabulary word of the day</li>
  </ol>
  <div class="email-field">Email Address</div>
  <div class="signup-btn">SIGN UP NOW !</div>
</section>

<footer class="site-footer">
  <div class="footer-brand"><span class="brand-dot"></span>Carla Winfield</div>
  <div class="cert-badge" role="img" aria-label="Certified trainer badge"><span></span></div>
  <nav class="social" aria-label="Social links">
    <a aria-label="Social link 1"></a><a aria-label="Social link 2"></a><a aria-label="Social link 3"></a><a aria-label="Social link 4"></a><a aria-label="Social link 5"></a>
  </nav>
  <div class="footer-rule"></div>
  <p class="copyright">Copyrights © 2017 Carla Winfield - All Rights Reserved.</p>
</footer>

</body>
</html>
```